we need a design for Water Bottle Lable Wrap
The product is called Calmora Springs is a restructured water. its a very healthy and rejuvenating water
we were looking at using as a tag ling Restore, Recover, Rejuvenate.

```html
<!DOCTYPE html>
<html lang="en">
<head>
<meta charset="utf-8">
<title>Calmora Springs – Bottle Label Wrap</title>
<link href="https://fonts.googleapis.com/css2?family=Montserrat:wght@500&display=swap" rel="stylesheet">
<style>
  :root {
    --page-bg: #ffffff;
    --sky-light: #e3effb;
    --sky-mid: #c9e2f8;
    --sky-cyan: #7fdcf9;
    --ink-slate: #4a5373;
    --mark-cyan: #62dcfb;
    --wave-deep: #1d4f96;
    --wave-mid: #3f7cc4;
    --wave-pale: #a9d2f3;
  }
  * { margin: 0; padding: 0; box-sizing: border-box; }
  html, body {
    width: 1200px;
    height: 2227px;
    overflow: hidden;
    background: var(--page-bg);
  }
  .canvas {
    position: relative;
    width: 1200px;
    height: 2227px;
  }
  .label-wrap {
    position: absolute;
    left: 121px;
    top: 680px;
    width: 958px;
    height: 867px;
    border-radius: 38px;
    overflow: hidden;
    background: linear-gradient(225deg, var(--sky-cyan) 0%, var(--sky-mid) 28%, var(--sky-light) 60%, var(--sky-mid) 100%);
    font-family: "Montserrat", sans-serif;
  }
  .water-splash {
    position: absolute;
    left: 0;
    right: 0;
    bottom: 0;
    height: 420px;
  }
  .water-splash svg { display: block; width: 100%; height: 100%; }
  .brand {
    position: absolute;
    left: 96px;
    top: 112px;
    display: flex;
    align-items: center;
    gap: 36px;
  }
  .brand-dot {
    width: 150px;
    height: 150px;
    border-radius: 50%;
    background: var(--mark-cyan);
  }
  .brand-name {
    font-weight: 500;
    font-size: 150px;
    line-height: 1;
    letter-spacing: -2px;
    color: var(--ink-slate);
  }
  .tagline {
    position: absolute;
    left: 224px;
    top: 334px;
    font-weight: 500;
    font-size: 28px;
    letter-spacing: 0.5px;
    color: var(--ink-slate);
  }
</style>
</head>
<body>
  <main class="canvas">
    <section class="label-wrap">
      <div class="water-splash" role="img" aria-label="Photograph of a clear blue water splash with droplets">
        <svg viewBox="0 0 958 420" preserveAspectRatio="none">
          <defs>
            <linearGradient id="splashFill" x1="0" y1="0" x2="0" y2="1">
              <stop offset="0" stop-color="var(--wave-mid)"/>
              <stop offset="0.45" stop-color="var(--wave-deep)"/>
              <stop offset="0.8" stop-color="var(--wave-pale)"/>
              <stop offset="1" stop-color="var(--sky-mid)"/>
            </linearGradient>
          </defs>
          <path d="M0 110 C180 120 380 170 560 230 C700 275 820 200 958 120 L958 420 L0 420 Z" fill="url(#splashFill)"/>
        </svg>
      </div>
      <div class="brand">
        <span class="brand-dot"></span>
        <span class="brand-name">Calmora</span>
      </div>
      <p class="tagline">RESTORE, RECOVER, REJUVENATE</p>
    </section>
  </main>
</body>
</html>
```